Window cleaning and Pressure washing

Truck wrap partial or full/background:
Would like to see a background of a water mark or something related to window cleaning. And or pressure washing.

Doors of the truck:
Need to have my logo printed in big on the doors and with LLC in small after the logo. Need to have my slogan below my logo on the door.
Slogan is; “Affordable 5 star services!”

Sides of the truck:
Want to see window cleaning and Pressure washing on the sides of the truck in big letters with the phone number. Slanted with a shadow effect.
(Would like to see slanted and not slanted) also need to see something that signifies 100% satisfaction or your money back!Preferably a sticker, Or a combination of both. Also need to have residential and commercial somewhere.
Phone number needs to be on here.

Tailgate:
Want to have the services on the back tailgate with the slogan, as well as the 100% money back guarantee sticker.
And the phone number here to!

Back window;
Needs to have the same background as the wrap on the truck or very slimier with the water swiped away Clean with the logo presented as shown in one of the pictures below.

```html
<!DOCTYPE html>
<html lang="en">
<head>
<meta charset="utf-8">
<title>The Clear Path LLC – Truck Wrap</title>
<link rel="stylesheet" href="https://fonts.googleapis.com/css2?family=Anton&family=Montserrat:wght@600;800&family=Oswald:wght@500;700&display=swap">
<style>
  :root {
    --water-light: #d4ecf6;
    --water-mid: #b6dcec;
    --water-deep: #9fcfe4;
    --brand-blue: #0d4f96;
    --sky-blue: #2f9fdb;
    --orange: #fcad0c;
    --ink: #111111;
    --charcoal: #333333;
    --silver: #b9bcbf;
    --white: #ffffff;
  }
  html, body { margin: 0; padding: 0; overflow: hidden; background: var(--white); }
  .wrap-sheet { display: block; width: 1098px; height: 1200px; }
  .logo-name { font-family: "Montserrat", sans-serif; font-weight: 800; fill: var(--ink); }
  .logo-llc { font-family: "Montserrat", sans-serif; font-weight: 800; fill: var(--ink); }
  .slogan { font-family: "Montserrat", sans-serif; font-weight: 800; }
  .licensed { font-family: "Montserrat", sans-serif; font-weight: 800; fill: var(--ink); }
  .licensed-tag { font-family: "Montserrat", sans-serif; font-weight: 800; fill: var(--white); letter-spacing: 10px; }
  .headline { font-family: "Anton", sans-serif; fill: var(--brand-blue); }
  .phone { font-family: "Anton", sans-serif; }
  .segment { font-family: "Montserrat", sans-serif; font-weight: 800; fill: var(--white); }
  .service { font-family: "Oswald", sans-serif; font-weight: 700; fill: var(--brand-blue); }
  .badge-big { font-family: "Anton", sans-serif; fill: var(--orange); }
  .badge-line { font-family: "Oswald", sans-serif; font-weight: 500; }
  .small-label { font-family: "Montserrat", sans-serif; font-weight: 600; fill: var(--ink); }
  .maker-name { font-family: "Montserrat", sans-serif; font-weight: 800; fill: #8a8f94; }
</style>
</head>
<body>
<svg class="wrap-sheet" viewBox="0 0 1834 2003" xmlns="http://www.w3.org/2000/svg">
  <defs>
    <linearGradient id="waterGradient" x1="0" y1="0" x2="1" y2="1">
      <stop offset="0" stop-color="var(--water-light)"/>
      <stop offset="0.5" stop-color="var(--water-mid)"/>
      <stop offset="1" stop-color="var(--water-light)"/>
    </linearGradient>
    <linearGradient id="fadeBand" x1="0" y1="0" x2="1" y2="0">
      <stop offset="0" stop-color="var(--white)" stop-opacity="0"/>
      <stop offset="0.3" stop-color="var(--white)"/>
      <stop offset="1" stop-color="var(--white)"/>
    </linearGradient>
    <linearGradient id="darkBand" x1="0" y1="0" x2="1" y2="0">
      <stop offset="0" stop-color="var(--ink)"/>
      <stop offset="0.75" stop-color="var(--ink)"/>
      <stop offset="1" stop-color="var(--ink)" stop-opacity="0"/>
    </linearGradient>
    <linearGradient id="scenePhoto" x1="0" y1="0" x2="1" y2="1">
      <stop offset="0" stop-color="#8c9aa3"/>
      <stop offset="0.5" stop-color="#c9d4cf"/>
      <stop offset="1" stop-color="#8fae6a"/>
    </linearGradient>
    <linearGradient id="silverBar" x1="0" y1="0" x2="1" y2="1">
      <stop offset="0" stop-color="#e8e9ea"/>
      <stop offset="1" stop-color="#8d9094"/>
    </linearGradient>
  </defs>

  <!-- ===== Side / door panel ===== -->
  <g class="side-panel">
    <path role="img" aria-label="Water droplet texture background"
      fill="url(#waterGradient)" fill-rule="evenodd"
      d="M87,415 L110,385 L460,336 L545,325 Q640,240 745,183 L985,167 Q1000,170 1005,190 L1022,340 L1755,335 L1750,390 L1700,395 L1700,515 L1752,517 L1748,540 L1700,545 L1690,640 L1565,652 L1565,560 Q1500,460 1390,460 Q1270,460 1240,560 L1240,635 L515,652 L490,560 Q460,470 330,470 Q215,470 205,510 L173,512 L173,412 Z
         M590,340 Q600,300 720,215 L900,188 Q930,187 930,215 L935,360 L610,365 Q588,360 590,340 Z"/>
    <rect class="door-handle" x="838" y="408" width="90" height="16" rx="8" fill="var(--white)"/>
    <polygon class="accent-stripe" points="850,425 1060,340 1185,340 930,652 850,652" fill="var(--silver)" opacity="0.45"/>

    <text class="licensed" x="238" y="401" font-size="30">LICENSED AND</text>
    <rect x="238" y="408" width="220" height="35" fill="var(--orange)"/>
    <text class="licensed-tag" x="250" y="436" font-size="26">INSURED</text>

    <text class="logo-name" x="565" y="430" font-size="50">THE</text>
    <text class="logo-name" x="565" y="488" font-size="62">CLEAR</text>
    <text class="logo-name" x="600" y="528" font-size="46">PATH <tspan class="logo-llc" font-size="22">LLC</tspan></text>

    <polygon points="480,542 890,542 870,585 500,585" fill="url(#fadeBand)"/>
    <text class="slogan" x="575" y="577" font-size="36" fill="var(--ink)">AFFORDABLE</text>
    <polygon points="545,588 1130,588 1100,640 570,640" fill="url(#darkBand)"/>
    <text class="slogan" x="592" y="627" font-size="40" fill="var(--white)">5 STAR SERVICES!</text>

    <g transform="skewX(-6)">
      <text class="headline" x="995" y="411" font-size="56">WINDOW</text>
      <text class="headline" x="1000" y="467" font-size="56">CLEANING AND</text>
      <text class="headline" x="1005" y="523" font-size="56">PRESSURE</text>
      <text class="headline" x="1012" y="579" font-size="56">WASHING</text>
    </g>

    <path d="M1205,340 L1755,335 L1750,390 L1700,395 L1690,420 L1250,420 Z" fill="var(--orange)"/>
    <circle cx="1231" cy="379" r="28" fill="var(--sky-blue)" stroke="var(--white)" stroke-width="5"/>
    <path d="M1220,366 l6,-3 l6,10 l-5,4 q4,9 10,13 l4,-4 l9,7 l-3,6 q-6,4 -14,-1 q-12,-9 -16,-20 q-2,-8 3,-12 Z" fill="var(--white)"/>
    <text class="phone" x="1282" y="405" font-size="66" fill="var(--white)" stroke="var(--charcoal)" stroke-width="2" transform="skewX(-4) translate(28 0)">(555) 214-3980</text>
    <rect x="1317" y="416" width="335" height="34" rx="3" fill="var(--sky-blue)"/>
    <text class="segment" x="1485" y="441" font-size="22" text-anchor="middle">Commercial &amp; Residential</text>

    <g class="guarantee-sticker">
      <text class="badge-big" x="1630" y="512" font-size="46" text-anchor="middle" stroke="var(--charcoal)" stroke-width="1">100%</text>
      <rect x="1573" y="516" width="114" height="36" rx="8" fill="var(--charcoal)"/>
      <text class="badge-line" x="1630" y="532" font-size="13" text-anchor="middle" fill="var(--white)">SATISFACTION OR</text>
      <rect x="1582" y="536" width="96" height="12" fill="var(--white)"/>
      <text class="badge-line" x="1630" y="546" font-size="10" text-anchor="middle" fill="var(--sky-blue)">YOUR MONEY BACK!</text>
      <text x="1630" y="574" font-size="14" text-anchor="middle" fill="#f7d20a">★★★★★</text>
    </g>
    <text class="small-label" x="1630" y="600" font-size="13" text-anchor="middle">Follow Us</text>
    <circle cx="1615" cy="619" r="11" fill="var(--ink)"/>
    <circle cx="1645" cy="619" r="11" fill="var(--ink)"/>
  </g>

  <!-- ===== Tailgate ===== -->
  <g class="tailgate">
    <path role="img" aria-label="Water droplet texture background"
      fill="url(#waterGradient)" fill-rule="evenodd"
      d="M292,790 L320,790 L325,845 L1525,845 L1530,795 L1555,795 L1555,1270 L292,1270 Z
         M828,865 L1018,865 Q1038,865 1036,885 L1030,945 Q1026,965 1006,965 L840,965 Q820,965 816,945 L810,885 Q808,865 828,865 Z"/>

    <g class="service-list">
      <g fill="none" stroke="var(--orange)" stroke-width="4">
        <circle cx="365" cy="907" r="18"/><path d="M356,907 l6,6 l11,-12"/>
        <circle cx="365" cy="978" r="18"/><path d="M356,978 l6,6 l11,-12"/>
        <circle cx="365" cy="1049" r="18"/><path d="M356,1049 l6,6 l11,-12"/>
        <circle cx="1108" cy="907" r="18"/><path d="M1099,907 l6,6 l11,-12"/>
        <circle cx="1108" cy="978" r="18"/><path d="M1099,978 l6,6 l11,-12"/>
        <circle cx="1108" cy="1049" r="18"/><path d="M1099,1049 l6,6 l11,-12"/>
      </g>
      <text class="service" x="403" y="926" font-size="50">WINDOW CLEANING</text>
      <text class="service" x="403" y="997" font-size="50">HOUSE WASHING</text>
      <text class="service" x="403" y="1068" font-size="50">PRESSURE WASHING</text>
      <text class="service" x="1146" y="926" font-size="50">ROOF CLEANING</text>
      <text class="service" x="1146" y="997" font-size="50">GUTTER CLEANING</text>
      <text class="service" x="1146" y="1068" font-size="50">SCREEN REPAIRS</text>
    </g>

    <text class="maker-name" x="922" y="1046" font-size="26" text-anchor="middle">KESTREL</text>

    <path d="M286,1122 L1255,1122 Q1270,1122 1278,1135 L1325,1270 L292,1270 Z" fill="var(--orange)"/>
    <path d="M286,1122 L360,1122 L447,1270 L292,1270 Z" fill="var(--charcoal)"/>
    <circle cx="387" cy="1193" r="47" fill="var(--orange)" stroke="var(--white)" stroke-width="7"/>
    <path d="M370,1172 l9,-5 l10,16 l-8,6 q6,14 16,21 l7,-6 l14,11 l-5,9 q-10,6 -22,-2 q-19,-14 -25,-32 q-3,-12 4,-18 Z" fill="var(--white)"/>
    <text class="phone" x="482" y="1240" font-size="118" fill="var(--white)" stroke="var(--charcoal)" stroke-width="2">(555) 214-3980</text>

    <g class="guarantee-sticker">
      <text class="badge-big" x="1414" y="1146" font-size="70" text-anchor="middle" stroke="var(--charcoal)" stroke-width="1.5">100%</text>
      <rect x="1325" y="1150" width="178" height="62" rx="14" fill="var(--charcoal)"/>
      <path d="M1340,1212 L1490,1212 L1478,1224 L1352,1224 Z" fill="var(--sky-blue)"/>
      <text class="badge-line" x="1414" y="1178" font-size="22" text-anchor="middle" fill="var(--white)">SATISFACTION OR</text>
      <rect x="1336" y="1184" width="156" height="22" fill="var(--white)"/>
      <text class="badge-line" x="1414" y="1201" font-size="17" text-anchor="middle" fill="var(--ink)">YOUR MONEY BACK!</text>
      <text x="1414" y="1244" font-size="24" text-anchor="middle" fill="#f7d20a">★★★★★</text>
    </g>
  </g>

  <!-- ===== Back window ===== -->
  <g class="back-window">
    <path role="img" aria-label="Water droplet texture background"
      fill="url(#waterGradient)"
      d="M500,1495 Q700,1455 1330,1468 Q1370,1475 1385,1520 L1422,1800 L420,1800 L480,1520 Q485,1500 500,1495 Z"/>
    <path role="img" aria-label="Photo of a gloved hand squeegeeing a soapy window in front of a house"
      fill="url(#scenePhoto)"
      d="M1100,1468 L1330,1468 Q1370,1475 1385,1520 L1422,1800 L870,1800 Z"/>
    <polygon class="accent-stripe" points="1075,1466 1140,1466 870,1800 805,1800" fill="url(#silverBar)"/>
    <text class="logo-name" x="525" y="1610" font-size="64">THE</text>
    <text class="logo-name" x="545" y="1696" font-size="92">CLEAR</text>
    <text class="logo-name" x="635" y="1756" font-size="64">PATH</text>
  </g>
</svg>
</body>
</html>
```